Website re-design for Brightmoor LLC website ( has existing website )

Looking to do a complete re-design of Brightmoorllc. The existing website is dated and built in wordpress. The new website will not be wordpress. The project folder includes an overview.txt file with details on the project. The file also contains a list of websites that he/she likes which I am sure is very helpful .
Number of Pages Required
1 page

```html
<!DOCTYPE html>
<html lang="en">
<head>
<meta charset="utf-8">
<title>Brightmoor LLC — Lake Weed Removal</title>
<link href="https://fonts.googleapis.com/css2?family=Montserrat:wght@400;500;600;700;800&family=Lato:wght@400;700&display=swap" rel="stylesheet">
<style>
:root{
  --blue:#0f5cad;
  --blue-dark:#0b4d93;
  --sky:#2a8fd6;
  --ink:#222;
  --muted:#444;
  --line:#7ea6d3;
  --grey-band:#f0f0f0;
  --faq-band:#eaf2f6;
  --footer:#1f1f1f;
  --white:#fff;
}
*{margin:0;padding:0;box-sizing:border-box}
html,body{width:1200px;height:4338px;overflow:hidden;background:var(--white)}
body{position:relative;font-family:'Lato',sans-serif;color:var(--ink)}
.abs{position:absolute}
.btn{position:absolute;background:var(--blue);color:var(--white);font-family:'Montserrat',sans-serif;font-weight:600;font-size:14px;display:flex;align-items:center;justify-content:center;letter-spacing:.3px}
.photo{position:absolute}

/* header */
.brand{position:absolute;font-family:'Montserrat',sans-serif;font-weight:600;font-size:27px;line-height:1;color:var(--blue)}
.brand.on-dark{color:var(--white)}
.call{left:758px;top:14px;display:flex;gap:8px;align-items:center}
.call small{display:block;font-family:'Montserrat',sans-serif;font-size:11px;font-weight:600;color:var(--ink)}
.call strong{font-family:'Montserrat',sans-serif;font-size:17px;color:var(--blue);font-weight:700}
.main-nav{position:absolute;top:64px;left:383px;display:flex;gap:27px;font-family:'Montserrat',sans-serif;font-size:12px;font-weight:600;color:var(--ink)}
.main-nav .on{color:var(--blue);border-bottom:2px solid var(--blue);padding-bottom:3px}

/* hero */
.hero{position:absolute;left:0;top:93px;width:1200px;height:535px;background:linear-gradient(180deg,#5d7a3d 0%,#48663a 40%,#3d4e35 75%,#4a5243 100%)}
.hero-kicker{position:absolute;width:1200px;text-align:center;color:var(--white);font-family:'Montserrat',sans-serif;font-weight:700;font-size:23px}
.hero-title{position:absolute;width:1200px;text-align:center;color:var(--white);font-family:'Montserrat',sans-serif;font-weight:800;font-size:50px;letter-spacing:1px}
.hero-dots{position:absolute;left:568px;display:flex;gap:6px}
.hero-dots i{width:8px;height:8px;background:var(--white);display:block}
.hero-dots i.on{background:var(--sky);outline:2px solid var(--white)}

/* titles */
.sec-title{position:absolute;width:1200px;text-align:center;font-family:'Montserrat',sans-serif;font-weight:700;font-size:21px}
.sec-rule{position:absolute;left:585px;width:30px;height:2px;background:var(--blue)}

/* services */
.card{position:absolute;width:299px;height:240px;border:1.5px solid var(--line);text-align:center;padding-top:20px}
.card .icon{width:62px;height:56px;margin:0 auto;border-radius:8px;background:#d9e7f5}
.card h3{font-family:'Montserrat',sans-serif;font-size:13px;font-weight:700;margin-top:18px;line-height:19px;padding:0 20px}
.card p{font-size:13.5px;color:var(--muted);line-height:21px;margin:10px auto 0;width:235px}
.card a{position:absolute;left:0;right:0;bottom:26px;font-family:'Montserrat',sans-serif;font-weight:700;font-size:12px;color:var(--blue);text-decoration:underline}
.card.active{background:var(--blue);border-color:var(--blue);color:var(--white)}
.card.active p,.card.active a{color:var(--white)}
.card.active .icon{background:#3b7cc4}

/* welcome */
.welcome{position:absolute;left:0;top:1536px;width:1200px;height:492px;background:var(--grey-band)}
.welcome-fade{position:absolute;left:0;top:0;width:560px;height:492px;background:linear-gradient(90deg,#c9cdd0 0%,#e3e5e6 60%,var(--grey-band) 100%)}
.welcome-ring{position:absolute;left:133px;top:42px;width:396px;height:396px;border-radius:50%;border:2px solid var(--blue);padding:8px}
.welcome-ring div{width:100%;height:100%;border-radius:50%;background:linear-gradient(160deg,#8b98a0,#59666b 55%,#3d4a47)}
.welcome .kicker{position:absolute;left:580px;top:42px;font-family:'Montserrat',sans-serif;color:var(--sky);font-weight:700;font-size:19px}
.welcome h2{position:absolute;left:580px;top:68px;font-family:'Montserrat',sans-serif;color:var(--blue);font-weight:800;font-size:31px}
.welcome .rule{position:absolute;left:580px;top:124px;width:30px;height:2px;background:var(--blue)}
.welcome p{position:absolute;left:580px;width:490px;font-size:14.5px;line-height:22.5px;color:var(--ink)}

/* testimonials */
.quote-box{position:absolute;left:133px;top:2160px;width:459px;height:258px;border:1.5px solid var(--line);text-align:center}
.quote-box p{margin:26px auto 0;width:330px;color:var(--blue);font-size:15.5px;line-height:25.5px}
.quote-box .rule{width:28px;height:1.5px;background:var(--ink);margin:14px auto}
.quote-box cite{display:block;font-style:normal;font-size:12.5px;color:var(--muted);line-height:16px}
.qmark{position:absolute;font-family:Georgia,serif;font-size:34px;font-weight:700;color:var(--blue);line-height:1}
.t-dots{position:absolute;top:2445px;left:323px;display:flex;gap:13px}
.t-dots i{width:7px;height:7px;border-radius:50%;background:#555;display:block}
.t-dots i.on{background:var(--blue)}

/* faq */
.faq{position:absolute;left:0;top:2788px;width:1200px;height:502px;background:var(--faq-band)}
.faq h2{position:absolute;left:131px;top:60px;font-family:'Montserrat',sans-serif;font-weight:700;font-size:21px;color:var(--blue)}
.faq-list{position:absolute;left:133px;top:125px;width:504px;list-style:none}
.faq-list li{height:44px;border-bottom:1px solid #b9c3c8;display:flex;justify-content:space-between;align-items:center;font-family:'Montserrat',sans-serif;font-size:13px;font-weight:500;color:var(--ink)}
.faq-list li span:last-child{font-size:18px;font-weight:400;color:#333}

/* gallery */
.label{position:absolute;bottom:12px;font-family:'Montserrat',sans-serif;font-weight:700;font-size:15px;color:var(--white);letter-spacing:.5px}

/* footer */
.footer{position:absolute;left:0;top:4096px;width:1200px;height:242px;background:var(--footer)}
.foot-nav{position:absolute;left:232px;top:113px;display:flex;gap:25px;font-family:'Montserrat',sans-serif;font-size:13px;color:#e6e6e6}
.foot-rule{position:absolute;left:225px;top:152px;width:738px;height:1px;background:#555}
.follow{position:absolute;left:232px;top:185px;display:flex;align-items:center;gap:8px;font-family:'Montserrat',sans-serif;font-size:12.5px;color:#e6e6e6}
.follow span{margin-right:12px}
.follow i{width:24px;height:24px;background:var(--white);display:block}
.copy{position:absolute;right:240px;top:190px;font-family:'Montserrat',sans-serif;font-size:11px;color:#e6e6e6}
</style>
</head>
<body>

<header>
  <div class="brand" style="left:133px;top:32px">Brightmoor</div>
  <div class="abs call">
    <svg width="26" height="26" viewBox="0 0 24 24" fill="none" stroke="#0f5cad" stroke-width="1.6"><path d="M5 3h4l2 5-2.5 1.5a11 11 0 0 0 6 6L16 13l5 2v4a2 2 0 0 1-2 2A17 17 0 0 1 3 5a2 2 0 0 1 2-2z"/></svg>
    <div><small>CALL US</small><strong>(555) 014-2260</strong></div>
  </div>
  <div class="btn" style="left:943px;top:18px;width:124px;height:32px;font-size:12px">FREE ESTIMATE</div>
  <nav class="main-nav">
    <span class="on">HOME</span><span>SERVICES</span><span>ABOUT US</span><span>FAQS</span><span>EMPLOYMENT</span><span>TESTIMONIALS</span><span>GALLERY</span><span>CONTACT US</span>
  </nav>
</header>

<section class="hero" role="img" aria-label="Scuba divers wading through lily pads beside a dock">
  <div class="hero-kicker" style="top:281px">SPECIALIZING IN RESIDENTIAL &amp; COMMERCIAL</div>
  <div class="hero-title" style="top:312px">LAKE WEED REMOVAL</div>
  <div class="btn" style="left:532px;top:389px;width:116px;height:38px">READ MORE</div>
  <div class="hero-dots" style="top:493px"><i></i><i></i><i class="on"></i><i></i><i></i></div>
</section>

<section class="services">
  <h2 class="sec-title" style="top:662px">OUR SERVICES</h2>
  <div class="sec-rule" style="top:704px"></div>

  <div class="card" style="left:131px;top:736px"><div class="icon" role="img" aria-label="Swimmer icon"></div><h3>DOCK INSTALL AND<br>REMOVAL SERVICES</h3><p>Reclaim open water in front of your dock, beach, or boat slip!</p><a>READ MORE</a></div>
  <div class="card" style="left:450px;top:736px"><div class="icon" role="img" aria-label="Beach umbrella icon"></div><h3>CANOPY SERVICES</h3><p>Reclaim open water in front of your dock, beach, or boat slip!</p><a>READ MORE</a></div>
  <div class="card" style="left:769px;top:736px"><div class="icon" role="img" aria-label="Barge icon"></div><h3>BARGE SERVICES (FALL 2022)</h3><p>Reclaim open water in front of your dock, beach, or boat slip!</p><a>READ MORE</a></div>

  <div class="card" style="left:131px;top:995px"><div class="icon" role="img" aria-label="Lift crane icon"></div><h3>DOCK LIFT SERVICES (FALL 2022)</h3><p>Reclaim open water in front of your dock, beach, or boat slip!</p><a>READ MORE</a></div>
  <div class="card active" style="left:450px;top:995px"><div class="icon" role="img" aria-label="Water weed icon"></div><h3>AQUATIC WEED REMOVAL</h3><p>Reclaim open water in front of your dock, beach, or boat slip!</p><a>READ MORE</a></div>
  <div class="card" style="left:769px;top:995px"><div class="icon" role="img" aria-label="Beach icon"></div><h3>BEACH CLEAN UP SERVICES</h3><p>Continuous waves wash away sand from your beach to expose mud and larger rocks.</p><a>READ MORE</a></div>

  <div class="card" style="left:131px;top:1253px"><div class="icon" role="img" aria-label="Water trampoline icon"></div><h3>WATER TRAMPOLINE SERVICE</h3><p>Reclaim open water in front of your dock, beach, or boat slip!</p><a>READ MORE</a></div>
  <div class="card" style="left:450px;top:1253px"><div class="icon" role="img" aria-label="Mussel shell icon"></div><h3>ZEBRA MUSSEL REMOVAL</h3><p>This Invasive species is becoming an increasing risk to Minnesota waterways.</p><a>READ MORE</a></div>
  <div class="card" style="left:769px;top:1253px"><div class="icon" role="img" aria-label="Lost item icon"></div><h3>LOST ITEM SEARCH</h3><p>Have you dropped something of value in the water? From boat keys to tools to other items,</p><a>READ MORE</a></div>
</section>

<section class="welcome">
  <div class="welcome-fade" role="img" aria-label="Faded lakeshore scene"></div>
  <div class="welcome-ring"><div role="img" aria-label="Dock covered with removed lake weeds beside a diver"></div></div>
  <div class="kicker">WELCOME TO</div>
  <h2>BRIGHTMOOR LLC</h2>
  <div class="rule"></div>
  <p style="top:149px">Brightmoor LLC is a company formed in response to the increase in invasive species in Minnesota lakes and waterways. The impact of these fast-growing nuisances inspired our venture to effectively control unwanted lake weeds and create an enjoyable environment craved by waterfront property homeowners.</p>
  <p style="top:282px">We have partnered with The Compost Yard to recycle 100% of the lake weeds we remove. The types of materials used in compost have a huge impact on how long it takes to break down and how nutrient rich the end product will be.</p>
  <div class="btn" style="left:584px;top:399px;width:118px;height:37px">READ MORE</div>
</section>

<section class="testimonials">
  <h2 class="sec-title" style="top:2071px;color:var(--blue)">TESTIMONIALS</h2>
  <div class="sec-rule" style="top:2110px"></div>
  <div class="qmark" style="left:125px;top:2152px">&ldquo;</div>
  <blockquote class="quote-box">
    <p>Everyone used to jump off the water trampoline and instantly get tangled in lake weeds. We contacted Brightmoor and their SCUBA divers have now been solving our problem for the past 4 years!</p>
    <div class="rule"></div>
    <cite>Cedar Point Shore Association<br>(Pine Lake)</cite>
  </blockquote>
  <div class="qmark" style="left:577px;top:2395px">&rdquo;</div>
  <div class="t-dots"><i></i><i></i><i class="on"></i><i></i><i></i></div>
  <div class="photo" style="left:626px;top:2158px;width:440px;height:558px;background:linear-gradient(180deg,#2f7fd6 0%,#5aa0e4 35%,#2d5c8f 55%,#6d6a5a 100%)" role="img" aria-label="Boat lift and long wooden dock on a lake"></div>
  <div class="photo" style="left:375px;top:2505px;width:434px;height:234px;background:var(--white)"></div>
  <div class="photo" style="left:134px;top:2515px;width:226px;height:213px;background:linear-gradient(180deg,#303a52 0%,#c8704a 45%,#2a2f3a 65%,#2a241f 100%)" role="img" aria-label="Sunset over the lake with a dog on the dock"></div>
  <div class="photo" style="left:375px;top:2515px;width:424px;height:213px;background:linear-gradient(180deg,#6d8fc2 0%,#c5ccd2 45%,#8b8f92 70%,#6e5e45 100%)" role="img" aria-label="Work barge on a trailer outside a shop"></div>
</section>

<section class="faq">
  <h2>FAQ</h2>
  <ul class="faq-list">
    <li><span>How early do lake weeds start to grow?</span><span>+</span></li>
    <li><span>How fast do lake weeds grow?</span><span>+</span></li>
    <li><span>How big of an area can I treat?</span><span>+</span></li>
    <li><span>What if the treatment area encroaches your neighbor's shoreline?</span><span>+</span></li>
    <li><span>How long does each treatment last?</span><span>+</span></li>
    <li><span>I DO NOT have a natural beach. Can I install one?</span><span>+</span></li>
  </ul>
  <div class="photo" style="left:973px;top:0;width:227px;height:502px;background:linear-gradient(180deg,#4c7a33,#3b5a2b 60%,#33482a)" role="img" aria-label="Shoreline trees"></div>
  <div class="photo" style="left:720px;top:109px;width:460px;height:338px;background:linear-gradient(180deg,#8fa7b3 0%,#3d6b92 35%,#2f4f74 60%,#6d6b3e 100%)" role="img" aria-label="Clear shallow water beside a dock with a kayak"></div>
</section>

<section class="gallery">
  <h2 class="sec-title" style="top:3335px;color:var(--blue)">PHOTO GALLERY</h2>
  <div class="sec-rule" style="top:3374px"></div>
  <div class="photo" style="left:134px;top:3412px;width:462px;height:280px;background:linear-gradient(180deg,#8a9aa5 0%,#3e6a86 30%,#4b5f55 65%,#9a8a55 100%)" role="img" aria-label="Weedy shoreline before cleanup"><span class="label" style="right:12px">BEFORE</span></div>
  <div class="photo" style="left:604px;top:3412px;width:462px;height:280px;background:linear-gradient(180deg,#5c6a55,#4a5a48 50%,#525b45)" role="img" aria-label="Clear lake water after cleanup"><span class="label" style="right:12px">AFTER</span></div>
  <div class="photo" style="left:134px;top:3704px;width:231px;height:276px;background:linear-gradient(180deg,#c9d3dc 0%,#5f7d45 35%,#8c8270 70%,#6d6455 100%)" role="img" aria-label="Dock surrounded by weeds before removal"><span class="label" style="right:26px">BEFORE</span></div>
  <div class="photo" style="left:365px;top:3704px;width:231px;height:276px;background:linear-gradient(180deg,#6f8f4d 0%,#4f6e3a 35%,#8e8676 70%,#766b5b 100%)" role="img" aria-label="Clear dock after weed removal"><span class="label" style="right:12px">AFTER</span></div>
  <div class="photo" style="left:604px;top:3704px;width:226px;height:276px;background:linear-gradient(180deg,#b6c4d2 0%,#6c7d86 40%,#5d6a5d 75%,#7d5e44 100%)" role="img" aria-label="Boat lift frame in weedy water before cleanup"><span class="label" style="right:12px">BEFORE</span></div>
  <div class="photo" style="left:830px;top:3704px;width:236px;height:276px;background:linear-gradient(180deg,#7e95b2 0%,#8ea1b1 40%,#5a6d7a 75%,#4f5f69 100%)" role="img" aria-label="Clear water around boat lift after cleanup"><span class="label" style="right:22px">AFTER</span></div>
  <div class="btn" style="left:520px;top:4023px;width:160px;height:37px">VIEW ALL IMAGES</div>
</section>

<footer class="footer">
  <div class="brand on-dark" style="left:225px;top:49px">Brightmoor</div>
  <div class="btn" style="left:840px;top:46px;width:123px;height:32px;font-size:12px">FREE ESTIMATE</div>
  <nav class="foot-nav"><span>HOME</span><span>SERVICES</span><span>ABOUT US</span><span>FAQS</span><span>EMPLOYMENT</span><span>TESTIMONIALS</span><span>GALLERY</span><span>CONTACT US</span></nav>
  <div class="foot-rule"></div>
  <div class="follow"><span>FOLLOW US</span><i></i><i></i><i></i></div>
  <div class="copy">Copyright © 2022 All Rights Reserved</div>
</footer>

</body>
</html>
```